Veltrane Group Business Card Design

The CEO is looking for a new trendy look for his business card.
You can stay with current branding or come up with something new/creative. It can be 3D, including Medical Office buildings. You can use our logo in a variety of colors. Please include name, title, company name, company website, email address, cell number

Target Market(s)

Real Estate Development and Construction

Industry/Entity Type

Health care real estate

Contact Information for Business Card

Rohesh Kamdar, CEO M-604.781.2249 E-roheshkamdar@veltrane.com Address:4180 Lindqvist Ave, Tampa, FL 33482 www.veltrane.com

Font styles to use
Other font styles liked:
• Be creative

Requirements
Must have
• Creative, trendy look
Nice to have
• Please go to our website to get a feel- www. veltrane.com
Should not have
• small fonts

```html
<!DOCTYPE html>
<html lang="en">
<head>
<meta charset="utf-8">
<title>Veltrane Group – Business Card</title>
<link rel="stylesheet" href="https://fonts.googleapis.com/css2?family=Montserrat:wght@400;500;700;800&display=swap">
<style>
  :root {
    --page: #e4e0da;
    --card: #efe8de;
    --ink-dark: #1e1b1a;
    --brand-red: #a8191e;
    --brand-navy: #1f3352;
    --text-light: #d8cec2;
  }
  html, body {
    margin: 0;
    width: 1200px;
    height: 1047px;
    overflow: hidden;
    background: var(--page);
    font-family: "Montserrat", sans-serif;
  }
  .business-card {
    position: absolute;
    left: 100px;
    top: 251px;
    width: 1000px;
    height: 545px;
    border-radius: 24px;
    overflow: hidden;
    background: var(--card);
    box-shadow: 0 10px 30px rgba(0,0,0,0.15);
  }
  .card-waves {
    position: absolute;
    inset: 0;
    width: 100%;
    height: 100%;
  }
  .wordmark {
    position: absolute;
    right: 40px;
    top: 48px;
    margin: 0;
    font-weight: 800;
    font-size: 56px;
    letter-spacing: -1px;
    color: var(--brand-red);
    line-height: 1;
  }
  .name-bar {
    position: absolute;
    left: 3px;
    top: 205px;
    width: 20px;
    height: 38px;
    background: var(--brand-red);
  }
  .holder-name {
    position: absolute;
    left: 40px;
    top: 204px;
    margin: 0;
    font-weight: 700;
    font-size: 34px;
    letter-spacing: 0.5px;
    color: var(--brand-red);
    text-transform: uppercase;
    line-height: 1.1;
  }
  .holder-title {
    position: absolute;
    left: 40px;
    top: 248px;
    margin: 0;
    font-weight: 400;
    font-size: 24px;
    letter-spacing: 1px;
    color: var(--text-light);
  }
  .address {
    position: absolute;
    left: 40px;
    top: 304px;
    margin: 0;
    font-style: normal;
    font-size: 25px;
    line-height: 39px;
    color: var(--text-light);
  }
  .contact-list {
    position: absolute;
    left: 40px;
    top: 402px;
    margin: 0;
    padding: 0;
    list-style: none;
    font-size: 24px;
    color: var(--text-light);
  }
  .contact-list li {
    display: flex;
    align-items: center;
    height: 39px;
  }
  .contact-icon {
    width: 20px;
    height: 20px;
    margin-right: 14px;
    flex: none;
  }
</style>
</head>
<body>
  <article class="business-card">
    <svg class="card-waves" viewBox="0 0 1000 545" preserveAspectRatio="none" aria-hidden="true">
      <path fill="var(--brand-red)" d="M0,46 C250,30 420,100 560,210 C700,310 850,342 1000,338 L1000,384 C820,386 680,332 540,236 C420,152 260,64 0,54 Z"/>
      <path fill="var(--brand-navy)" d="M0,60 C250,58 400,124 530,242 C680,362 840,396 1000,395 L1000,428 C810,432 660,382 510,272 C380,172 250,100 0,92 Z"/>
      <path fill="var(--ink-dark)" d="M0,102 C250,110 380,182 500,282 C650,402 820,446 1000,440 L1000,545 L0,545 Z"/>
    </svg>

    <p class="wordmark">Veltrane Group</p>

    <span class="name-bar"></span>
    <h1 class="holder-name">Rohesh Kamdar</h1>
    <p class="holder-title">CEO</p>

    <address class="address">4180 Lindqvist Ave,<br>Tampa, FL 33482</address>

    <ul class="contact-list">
      <li>
        <svg class="contact-icon" viewBox="0 0 20 20" aria-hidden="true"><rect x="5" y="1" width="10" height="18" rx="2" fill="none" stroke="var(--brand-red)" stroke-width="2"/><circle cx="10" cy="15.5" r="1.2" fill="var(--brand-red)"/></svg>
        604.781.2249
      </li>
      <li>
        <svg class="contact-icon" viewBox="0 0 20 20" aria-hidden="true"><rect x="1" y="5" width="18" height="11" fill="var(--brand-red)"/><path d="M1,5 L10,12 L19,5" fill="none" stroke="var(--ink-dark)" stroke-width="1.5"/></svg>
        roheshkamdar@veltrane.com
      </li>
      <li>
        <svg class="contact-icon" viewBox="0 0 20 20" aria-hidden="true"><circle cx="10" cy="10" r="8.5" fill="var(--brand-red)"/><path d="M1.5,10 H18.5 M10,1.5 C6,6 6,14 10,18.5 M10,1.5 C14,6 14,14 10,18.5" fill="none" stroke="var(--ink-dark)" stroke-width="1.2"/></svg>
        www.veltrane.com
      </li>
    </ul>
  </article>
</body>
</html>
```